Promotional brochure for educational consulting firm

Updates

Hi Designers!

Please do a 8.5 x 11 inch tri-fold brochure as well as a 8.5 x 11 inch half-fold brochure.  I appreciate black and white versions in addition to color.  Please take a look at my company's website for a better sense of the look and feel I am going for:  www.brightlanepa.org

Thanks!

Industry/Entity Type

Consulting

Colors
3176b5
85abd2
fcfbfd

```html
<!DOCTYPE html>
<html lang="en">
<head>
<meta charset="utf-8">
<title>Brightlane Associates – Tri-fold Brochure</title>
<link href="https://fonts.googleapis.com/css2?family=Montserrat:wght@400;600;700&family=Quicksand:wght@400;500&display=swap" rel="stylesheet">
<style>
  :root {
    --brand-blue: #3176b5;
    --deep-blue: #23578f;
    --navy: #1f3f6b;
    --sky: #85abd2;
    --sky-light: #a9c4e2;
    --paper: #fcfbfd;
    --ink: #1d2a3a;
    --canvas-bg: #e9ebee;
  }
  * { margin: 0; padding: 0; box-sizing: border-box; }
  html, body { width: 1200px; height: 1000px; overflow: hidden; background: var(--canvas-bg); }
  body { font-family: "Montserrat", Arial, sans-serif; color: var(--ink); }

  .brochure {
    position: absolute; left: 50px; top: 75px;
    width: 1100px; height: 850px;
    display: flex;
    box-shadow: 0 12px 30px rgba(0,0,0,.18);
    background: var(--paper);
  }
  .panel { position: relative; width: 366.67px; height: 850px; overflow: hidden; }
  .panel + .panel { border-left: 1px solid rgba(0,0,0,.06); }
  .panel svg.shape { position: absolute; left: 0; width: 100%; display: block; }

  /* Panel 1 – services */
  .photo-pencils {
    position: absolute; left: 0; top: 0; width: 100%; height: 540px;
    background: linear-gradient(160deg, #c98a6d 0%, #d9b16a 25%, #b9445a 50%, #6f4fa8 75%, #3b6bb0 100%);
  }
  .photo-pencils::after {
    content: ""; position: absolute; inset: 0;
    background: linear-gradient(180deg, rgba(255,255,255,.25), rgba(255,255,255,.05));
  }
  .quote {
    position: absolute; left: 36px; right: 30px; top: 130px;
    font-family: "Quicksand", Arial, sans-serif; font-weight: 500;
    font-size: 25px; line-height: 1.75; color: var(--ink);
  }
  .quote .mark { font-family: Georgia, serif; font-size: 44px; font-weight: 700; line-height: 0; vertical-align: -8px; margin-right: 4px; }
  .services-area { position: absolute; left: 0; bottom: 0; width: 100%; height: 330px; background: var(--deep-blue); }
  .services-title {
    position: absolute; left: 36px; top: 540px;
    font-size: 30px; font-weight: 600; color: var(--paper);
  }
  .services-list {
    position: absolute; left: 40px; top: 600px; list-style: none;
    font-size: 15px; font-weight: 600; color: var(--sky-light);
  }
  .services-list li { line-height: 23.5px; padding-left: 26px; position: relative; }
  .services-list li::before {
    content: ""; position: absolute; left: 0; top: 10px; width: 4px; height: 4px;
    border-radius: 50%; background: var(--paper);
  }

  /* Shared cover pieces */
  .top-band { position: absolute; left: 0; top: 0; width: 100%; height: 300px; background: linear-gradient(180deg, var(--sky) 0%, var(--sky-light) 100%); }
  .photo { position: absolute; left: 0; width: 100%; }
  .photo-crayons { top: 280px; height: 200px; background: linear-gradient(135deg, #5b6b74 0%, #8a8e6a 35%, #d27a33 65%, #c8382e 100%); }
  .photo-students { top: 280px; height: 180px; background: linear-gradient(135deg, #dfe6ee 0%, #9fbcd8 40%, #4a4e7a 75%, #2d2f55 100%); }
  .tagline-flag {
    position: absolute; left: 0; width: 100%; height: 34px;
    font-family: "Quicksand", Arial, sans-serif; font-size: 13px; color: var(--paper);
    display: flex; align-items: center; padding-left: 80px;
  }
  .identity {
    position: absolute; left: 0; width: 100%; text-align: center; color: var(--brand-blue);
  }
  .identity .dot { display: block; width: 62px; height: 62px; border-radius: 50%; background: var(--brand-blue); margin: 0 auto 14px; }
  .identity .name { font-size: 17px; font-weight: 600; letter-spacing: .5px; }
  .identity .sub { font-size: 11px; font-weight: 600; letter-spacing: .6px; text-transform: uppercase; margin-top: 3px; }
  .contact-band {
    position: absolute; left: 0; bottom: 0; width: 100%; height: 150px; background: var(--brand-blue);
    color: var(--paper); text-align: center; font-size: 14px; font-weight: 600; padding-top: 56px; line-height: 22px;
  }

  /* Panel 2 – resources */
  .resources { position: absolute; left: 36px; right: 20px; top: 40px; color: var(--paper); }
  .resources h2 { font-size: 19px; font-weight: 700; color: var(--ink); margin-bottom: 10px; }
  .resources ul { list-style: none; font-size: 11.5px; font-weight: 600; line-height: 23px; }

  /* Panel 3 – intro */
  .intro {
    position: absolute; left: 34px; right: 26px; top: 46px;
    font-size: 21px; font-weight: 700; line-height: 1.3; color: #1c2533;
  }
</style>
</head>
<body>
<main class="brochure">

  <section class="panel panel-services">
    <div class="photo-pencils" role="img" aria-label="Close-up photo of coloured pencil tips"></div>
    <p class="quote"><span class="mark">&ldquo;</span>We maintain a network of on-call, expert associates who are ready to assist school clients in a variety of key areas. Our areas of expertise include:</p>
    <svg class="shape" style="top:500px;height:60px" viewBox="0 0 367 60" preserveAspectRatio="none">
      <path d="M0 40 Q180 0 367 20 L367 60 L0 60 Z" fill="var(--deep-blue)"/>
    </svg>
    <div class="services-area"></div>
    <h2 class="services-title">Services</h2>
    <ul class="services-list">
      <li>Board Training</li>
      <li>Budget and Operations</li>
      <li>Capacity Reports</li>
      <li>Charter Development and Renewal</li>
      <li>Communications</li>
      <li>Leadership Assessment and Coaching</li>
      <li>Lender Negotiations</li>
      <li>Fund Development</li>
      <li>Placement of Interim Administrators</li>
    </ul>
  </section>

  <section class="panel panel-resources">
    <div class="photo photo-crayons" role="img" aria-label="Photo of crayons in colourful containers"></div>
    <div class="top-band"></div>
    <svg class="shape" style="top:260px;height:60px" viewBox="0 0 367 60" preserveAspectRatio="none">
      <path d="M0 0 L367 0 L367 10 Q200 60 0 40 Z" fill="var(--sky-light)"/>
    </svg>
    <div class="resources">
      <h2>Resources</h2>
      <ul>
        <li>Western Alliance of Independent Schools (WAIS)</li>
        <li>Pacific Charter Schools Network (PCSN)</li>
        <li>State Office of Public Learning</li>
        <li>Assessment Technology Readiness</li>
        <li>National Council of Private Schools (NCPS)</li>
        <li>National Faith-Based Schools Forum</li>
        <li>EduBridge</li>
      </ul>
    </div>
    <svg class="shape" style="top:440px;height:80px" viewBox="0 0 367 80" preserveAspectRatio="none">
      <path d="M0 40 Q180 20 367 0 L367 80 L0 80 Z" fill="var(--paper)"/>
      <path d="M60 30 L367 0 L367 22 L60 52 Z" fill="var(--brand-blue)"/>
    </svg>
    <div class="tagline-flag" style="top:450px">~School leadership is 24/7/365.</div>
    <div class="identity" style="top:545px">
      <span class="dot"></span>
      <div class="name">Brightlane Associates LLC</div>
      <div class="sub">Supporting Schools &amp; School Leaders</div>
    </div>
    <svg class="shape" style="top:680px;height:40px" viewBox="0 0 367 40" preserveAspectRatio="none">
      <path d="M0 40 Q200 10 367 0 L367 40 Z" fill="var(--brand-blue)"/>
    </svg>
    <div class="contact-band">555.014.2736 &nbsp;|&nbsp; 555.019.4410<br>info@brightlanepa.org</div>
  </section>

  <section class="panel panel-cover">
    <div class="photo photo-students" role="img" aria-label="Photo of two students studying a globe with a magnifying glass"></div>
    <div class="top-band"></div>
    <svg class="shape" style="top:260px;height:50px" viewBox="0 0 367 50" preserveAspectRatio="none">
      <path d="M0 0 L367 0 L367 10 Q200 50 0 30 Z" fill="var(--sky-light)"/>
    </svg>
    <h1 class="intro">Brightlane Associates LLC provides administrative and management consulting to schools in all stages of organizational growth.</h1>
    <svg class="shape" style="top:420px;height:80px" viewBox="0 0 367 80" preserveAspectRatio="none">
      <path d="M0 40 Q180 20 367 0 L367 80 L0 80 Z" fill="var(--paper)"/>
      <path d="M60 30 L367 0 L367 22 L60 52 Z" fill="var(--brand-blue)"/>
    </svg>
    <div class="tagline-flag" style="top:430px">~School leadership is 24/7/365.</div>
    <div class="identity" style="top:540px">
      <span class="dot"></span>
      <div class="name">Brightlane Associates LLC</div>
      <div class="sub">Supporting Schools &amp; School Leaders</div>
    </div>
    <svg class="shape" style="top:680px;height:40px" viewBox="0 0 367 40" preserveAspectRatio="none">
      <path d="M0 40 Q200 10 367 0 L367 40 Z" fill="var(--brand-blue)"/>
    </svg>
    <div class="contact-band">555.014.2736 &nbsp;|&nbsp; 555.019.4410<br>info@brightlanepa.org</div>
  </section>

</main>
</body>
</html>
```